SitePress Direct-Booking Website for Bend, Oregon Vacation Rental — $750 Budget
Project Overview

We are looking for a talented SitePress designer/developer to create a clean, professional and inviting direct-booking website for Birch Lantern Retreat, an established short-term vacation rental in Bend, Oregon.

The property is currently successfully listed on Staynest and Hoplo. Our Staynest property has approximately a 4.98-star rating with more than 200 reviews, is an Staynest Visitor Pick, and ranks among the Top 1% of eligible homes.

Project Budget: $750

We will select the designer based on the quality of the initial concept, understanding of the property, proposed booking solution and ability to deliver a completed and functioning SitePress website.

Existing Staynest Listing

Please use our current Staynest listing as the primary reference for photographs, property details, amenities and design inspiration:

https://www.staynest-example.net/rooms/48172036

Original high-resolution photographs and additional property information will be provided to the selected designer.

Design Direction

We want the website to feel:

Upscale but comfortable
Warm and welcoming
Clean and uncluttered
Pacific Northwest / Central Oregon
Professional rather than corporate
Highly visual with large property photographs
Easy to navigate
Excellent on phones, tablets and desktop computers

We welcome creativity and want designers to show us their vision for the property rather than simply copying our Staynest listing.

The website should immediately communicate that Birch Lantern Retreat is a highly rated vacation rental in an excellent Bend location.

Key Property Features
3 bedrooms
2 bathrooms
Sleeps up to 6 guests
Pet friendly
Approximately a 5-minute walk to Bend's Tannery Row Quarter
Near restaurants, shopping and Larkspur Fields Pavilion
Private fenced backyard
Covered outdoor area
Off-street driveway parking
Fireplace
Well-equipped kitchen
Staynest Prime Keeper
Staynest Visitor Pick
Top 1% of eligible Staynest homes
Approximately 4.98 stars with 200+ guest reviews

Our location, guest reviews, cleanliness, comfort, backyard, pet-friendly accommodations and walkability should be major selling points throughout the website.

Website Structure

We anticipate approximately 6–7 pages:

Home

Large hero photograph with a strong opening message and prominent BOOK DIRECT and CHECK AVAILABILITY buttons.

The home page should quickly communicate:

BIRCH LANTERN RETREAT — BEND, OREGON

3 Bedrooms | 2 Baths | Sleeps 6 | Pet Friendly | Walk to Tannery Row

Our exceptional guest rating and Staynest history should also be prominently featured.

The House

Bedrooms, bathrooms, kitchen, living areas, backyard and major amenities.

Photo Gallery

Large, attractive and fast-loading photographs with an easy-to-use mobile gallery.

Location / Explore Bend

Tannery Row Quarter, Larkspur Fields Pavilion, Deschutes River, restaurants, breweries, shopping, downtown Bend and nearby outdoor recreation.

Guest Reviews

Selected guest reviews and prominent presentation of our strong Staynest reputation.

Availability & Book Direct

A simple and professional direct-booking experience.

Contact / FAQ

Contact information plus common questions regarding pets, parking, check-in/check-out, cancellations and other policies.

IMPORTANT — Direct Booking & Credit Card Requirements

We want guests to be able to book directly through the website without having to contact us first.

The website should use a proven SitePress vacation-rental booking plugin or system rather than a custom-built reservation/payment system.

Guests should be able to:

Select arrival and departure dates
See available dates
Enter number of guests
See nightly charges
See cleaning fees
See applicable lodging taxes and other charges
See the complete reservation total before paying
Enter guest/contact information
Pay securely by credit or debit card
Receive an automatic reservation confirmation

Paywell is our preferred credit-card processor.

Credit-card information must be processed securely through Paywell or another established payment processor. Credit-card information should NOT be stored directly on our SitePress website.

Staynest & Hoplo Calendar Synchronization

This is very important.

The direct-booking calendar must synchronize with our existing Staynest and Hoplo calendars to reduce the possibility of double bookings.

For this single-property website, we prefer a simple solution using Staynest/Hoplo calendar or iCal synchronization rather than an expensive monthly channel-management service, if practical.

The designer should clearly identify the booking plugin/system they propose using.

IMPORTANT — Tell Us Your Proposed Booking Solution

As part of your submission, please tell us:

Which SitePress booking plugin/system you recommend.
Whether it synchronizes availability with Staynest and Hoplo.
Whether it integrates directly with Paywell.
The initial cost of the plugin/software.
Any annual or monthly fees.
Whether any additional paid software or services will be required.

We strongly prefer a solution with little or no ongoing monthly software expense.

We do not want to select a designer and later discover that the proposed booking system requires an expensive monthly subscription.

SitePress & Technical Requirements

The completed project should include:

Fully functioning SitePress website
Responsive desktop/tablet/mobile design
Fast-loading pages
Optimized photographs
SSL/HTTPS compatibility
Direct-booking functionality
Paywell payment integration
Staynest calendar synchronization
Hoplo calendar synchronization
Automatic booking confirmations
Cleaning fee and lodging-tax calculations
Contact form
Vizor Maps/location integration
Basic spam/security protection
Vizor Metrics capability
Basic SEO setup
Search-engine submission capability
Easy owner editing of text, rates and photographs
Search Engine Optimization

The website should be structured for Vizor and other search engines.

Important search themes include:

Bend Oregon vacation rental
Bend Oregon vacation home
Tannery Row Quarter vacation rental
Vacation rental near Tannery Row Bend
Bend Oregon pet-friendly vacation rental
Bend vacation rental near Larkspur Fields Pavilion
Bend Oregon direct booking vacation rental

We are not expecting an extensive ongoing SEO campaign for the $750 project. We do expect proper page titles, descriptions, headings, image optimization and a good technical foundation for future SEO.

Ownership

Upon completion and final payment:

We own the completed SitePress website.
We receive full SitePress administrator access.
We control the domain and hosting accounts.
We own all custom design files created for the project.
All necessary login credentials are provided to us.
The website can be moved to another SitePress hosting provider in the future.
There should be no proprietary dependency on the developer after completion.
What We Want From Contestants

Please review our Staynest listing before submitting your concept.

We are particularly interested in seeing an initial homepage concept showing how you would present:

Birch Lantern Retreat
The Bend / Tannery Row location
Our photography
Our exceptional guest reviews and ratings
The Book Direct message
The availability/booking call-to-action

We will provide feedback on the concepts we like and work with the selected designer to refine and complete the website.

Our Goal

Our objective is straightforward:

Create a beautiful, trustworthy and easy-to-use website that encourages guests to book Birch Lantern Retreat directly with us.

The website will complement—not replace—our existing Staynest and Hoplo listings.

We want repeat guests and new customers to have an easy way to find the property, check availability and book directly while receiving the same professional experience they expect from a major vacation-rental platform.

Target Market(s)

Consumers looking to to travel to Mexico for vacation. Family or couples

Industry/Entity Type

Short term vacation rental industry

Coding

Coded - Design and coding required

Number of Pages Required

5+ page

Requirements
Must have
• Capabilities to accept credit card payments and link to other rental property sites calendars such as HOPLO and Staynset
Nice to have
• Option for best plugins for property rental

```html
<!DOCTYPE html>
<html lang="en">
<head>
<meta charset="utf-8">
<title>Birch Lantern Retreat — Bend, Oregon Vacation Rental</title>
<link href="https://fonts.googleapis.com/css2?family=Gilda+Display&family=Plus+Jakarta+Sans:wght@400;500;600;700&display=swap" rel="stylesheet">
<style>
:root{
  --stage:#a3a3a3;
  --green:#3c5a1c;
  --green-dark:#2e4315;
  --green-deep:#25370f;
  --gold:#c98f0f;
  --cream:#f7f3ea;
  --cream-2:#f1ebdd;
  --ink:#2a2a22;
  --muted:#5e5d55;
  --line:#e4dccb;
  --white:#ffffff;
}
*{box-sizing:border-box;margin:0;padding:0}
html,body{width:858px;height:1200px;overflow:hidden;background:var(--stage)}
body{font-family:"Plus Jakarta Sans",sans-serif;color:var(--ink)}
.stage{position:absolute;left:0;top:0;width:1624px;height:2272px;transform:scale(.52833);transform-origin:0 0}
.column{position:absolute;width:631px;background:var(--white);overflow:hidden}
.column--left{left:196px;top:52px;height:2166px}
.column--right{left:894px;top:52px;height:1851px}
.a{position:absolute}
.eyebrow{font-size:7.5px;letter-spacing:1.4px;color:var(--gold);text-transform:uppercase}
.h2{font-family:"Gilda Display",serif;font-weight:400;font-size:23px;line-height:1.02;color:var(--green-dark)}
.center{text-align:center;left:0;right:0}
.ph{position:absolute;background:linear-gradient(150deg,#b7b3a6,#e6e1d6)}
.ph--yard{background:linear-gradient(160deg,#6f8f9a 0%,#587d3a 55%,#7a6a4e 100%)}
.ph--house{background:linear-gradient(170deg,#6d9ad0 0%,#8aa3ad 40%,#5c6a66 60%,#4b7a2a 100%)}
.ph--room{background:linear-gradient(160deg,#c9c6bb 0%,#ebe7dc 55%,#b8a68c 100%)}
.ph--teal{background:linear-gradient(160deg,#cbc8bc 0%,#e7e3d9 50%,#4f8f8c 100%)}
.ph--kitchen{background:linear-gradient(160deg,#e2dfd6 0%,#b9b5aa 50%,#7a5a3c 100%)}
.ph--patio{background:linear-gradient(160deg,#5b7c9b 0%,#7f6c52 55%,#8a7860 100%)}
.btn{position:absolute;display:flex;align-items:center;justify-content:center;gap:4px;font-size:7.5px;font-weight:700;letter-spacing:.6px;color:var(--white);text-transform:uppercase}
.btn--gold{background:var(--gold)}
.btn--green{background:var(--green)}
.btn--dark{background:var(--green-dark)}
.topbar{left:0;top:0;width:631px;height:16px;background:#27351a;color:#fff;font-size:5px}
.topbar span{position:absolute;top:5px}
.hero{left:0;top:16px;width:631px;height:336px;background:linear-gradient(180deg,#3f5a3a 0%,#596f4e 30%,#6f7f70 48%,#4f6e2c 75%,#3e5b22 100%)}
.hero__shade{left:0;top:0;width:631px;height:336px;background:linear-gradient(180deg,rgba(20,30,10,.45),rgba(20,30,10,.15) 55%,rgba(20,30,10,.25))}
.brand{font-family:"Gilda Display",serif;color:#fff;font-size:8.5px;letter-spacing:.3px;white-space:nowrap}
.nav a{position:absolute;top:43px;font-size:6px;color:#fff;text-decoration:none}
.hero__title{font-family:"Gilda Display",serif;font-weight:400;color:#fff;font-size:33px;line-height:35px}
.hero__meta{color:#fff;font-size:8.5px}
.stats{left:64px;top:380px;width:506px;height:88px;background:var(--cream);border:1px solid var(--line)}
.stats__inner{position:absolute;inset:4px;border:1px solid #eadfc4;display:flex}
.stat{flex:1;text-align:center;padding-top:10px;border-right:1px solid var(--line)}
.stat:last-child{border-right:0}
.stat__num{font-family:"Gilda Display",serif;font-size:16px;color:var(--ink);margin-top:3px}
.stat__lbl{font-size:7px;color:var(--muted);margin-top:3px}
.intro__para{font-size:5.6px;line-height:9.3px;color:var(--muted);width:222px}
.check{font-size:6.5px;color:var(--green-dark);font-weight:500}
.check::before{content:"✓ ";color:var(--gold);font-weight:700}
.features{left:0;top:806px;width:631px;height:364px;background:var(--cream)}
.fcard{position:absolute;width:122px;height:106px;background:#fff;text-align:center;font-size:7.5px;color:var(--ink);line-height:10px}
.fcard__icon{width:38px;height:38px;margin:22px auto 9px;border-radius:50%;background:var(--green);border:2px solid var(--gold);display:flex;align-items:center;justify-content:center}
.tile{position:absolute;background:var(--cream-2)}
.tile .ph{left:0;top:0;right:0;bottom:27px}
.tile__lbl{position:absolute;left:14px;bottom:7px;font-family:"Gilda Display",serif;font-size:11px;color:#4a4a40}
.outdoor{left:0;top:1840px;width:631px;height:326px;background:linear-gradient(135deg,#3f5d1c,#2f4a14)}
.ofeat{position:absolute;font-size:6.5px;color:#fff;display:flex;align-items:center;gap:7px}
.ofeat i{width:18px;height:18px;border-radius:50%;background:rgba(255,255,255,.15);display:block}
.location{left:0;top:0;width:631px;height:294px;background:var(--cream)}
.lcard{position:absolute;top:126px;width:114px;height:120px;background:#fff;border:1px solid var(--line);text-align:center;font-size:6.5px;line-height:10px;color:var(--muted)}
.lcard__frame{position:absolute;inset:3px;border:1px solid var(--gold)}
.lcard b{font-weight:500;color:var(--ink)}
.lcard svg{display:block;margin:20px auto 10px}
.testimonials{left:0;top:820px;width:631px;height:304px;background:var(--cream)}
.review{position:absolute;top:941px;width:163px;height:134px;background:#fff;border:1px solid var(--line);padding:10px 14px;font-size:5.6px;line-height:8.5px;color:var(--muted)}
.review__av{width:28px;height:28px;border-radius:50%;background:linear-gradient(160deg,#c9b49b,#8a6e56);float:left;margin-right:10px}
.review__name{font-size:7.5px;color:var(--ink);font-weight:500;padding-top:5px}
.review__stars{clear:both;color:var(--gold);font-size:7px;padding-top:8px;letter-spacing:1px}
.arrow{position:absolute;width:22px;height:22px;border-radius:50%;background:var(--gold);color:#fff;font-size:11px;display:flex;align-items:center;justify-content:center}
.faq__row{position:absolute;left:91px;width:430px;height:34px;border-bottom:1px solid var(--line);font-size:7.8px;color:var(--ink);padding-top:12px}
.faq__row::after{content:"+";position:absolute;right:2px;top:9px;width:14px;height:14px;border-radius:50%;background:var(--gold);color:#fff;font-size:11px;line-height:14px;text-align:center;font-weight:600}
.cta{left:52px;top:1459px;width:534px;height:200px;background:linear-gradient(135deg,#3d5a1e,#2c4213)}
.form{left:76px;top:114px;width:394px;height:30px;background:#fff;display:flex}
.form__field{flex:1;border-right:1px solid var(--line);padding:6px 0 0 26px;font-size:6px;color:var(--ink);position:relative}
.form__field small{display:block;font-size:4.8px;color:var(--gold);letter-spacing:.4px}
.form__field::before{content:"";position:absolute;left:12px;top:10px;width:9px;height:9px;border:1px solid #999;border-radius:1px}
.foot__head{font-family:"Gilda Display",serif;font-size:7px;color:var(--muted);letter-spacing:.6px}
.foot__list{font-size:5.6px;line-height:10.8px;color:var(--muted)}
.social{position:absolute;top:1746px;width:12px;height:12px;border-radius:50%;background:#2a2a22}
</style>
</head>
<body>
<div class="stage">

<div class="column column--left">
  <div class="a topbar">
    <span style="left:66px">● Bend, Oregon, United States</span>
    <span style="left:414px">✉ booking@birchlantern.example</span>
    <span style="left:512px">☎ +1 541 555 0142</span>
  </div>

  <div class="a hero" role="img" aria-label="Front yard photograph of the craftsman house with lawn, rocks and stone steps"></div>
  <div class="a hero__shade" style="top:16px"></div>
  <div class="a brand" style="left:58px;top:45px">BIRCH LANTERN RETREAT</div>
  <nav class="nav">
    <a style="left:203px">The House</a><a style="left:256px">Features</a><a style="left:304px">Photos</a><a style="left:345px">Explore Bend</a><a style="left:402px">FAQ</a><a style="left:436px">Contact</a>
  </nav>
  <div class="btn btn--gold" style="left:496px;top:36px;width:75px;height:19px;font-size:5.8px">Book Direct →</div>
  <div class="a center" style="top:108px;text-align:center;color:#fff;font-size:8.5px;letter-spacing:1.2px">BIRCH LANTERN RETREAT • BEND, OREGON</div>
  <h1 class="a center hero__title" style="top:124px;text-align:center">Your Bend Getaway,<br>Steps from Tannery Row</h1>
  <div class="a center hero__meta" style="top:203px;text-align:center">3 Bedrooms &nbsp;•&nbsp; 2 Bathrooms &nbsp;•&nbsp; Sleeps 6 &nbsp;•&nbsp; Near Tannery Row Quarter</div>
  <div class="btn btn--green" style="left:172px;top:233px;width:133px;height:31px">Check Availability →</div>
  <div class="btn btn--gold" style="left:317px;top:233px;width:134px;height:31px">Book Direct →</div>
  <svg class="a" style="left:309px;top:298px" width="12" height="24" viewBox="0 0 12 24"><rect x="2" y="1" width="8" height="13" rx="4" fill="none" stroke="#fff" stroke-width="1"/><path d="M3 17l3 3 3-3M3 20l3 3 3-3" fill="none" stroke="#fff" stroke-width="1"/></svg>

  <div class="a stats"><div class="stats__inner">
    <div class="stat"><svg width="16" height="16" viewBox="0 0 24 24"><path d="M12 2l3 7h7l-5.5 4.5 2 7.5-6.5-4.5-6.5 4.5 2-7.5L2 9h7z" fill="none" stroke="#444" stroke-width="1.3"/></svg><div class="stat__num">4.98</div><div class="stat__lbl">Guest Rating</div></div>
    <div class="stat"><svg width="16" height="16" viewBox="0 0 24 24"><path d="M12 3a9 8 0 1 0 0 16l5 3-1-4a9 8 0 0 0-4-15z" fill="none" stroke="#444" stroke-width="1.3"/></svg><div class="stat__num">200+</div><div class="stat__lbl">Guest Reviews</div></div>
    <div class="stat"><svg width="16" height="16" viewBox="0 0 24 24"><circle cx="12" cy="11" r="6" fill="none" stroke="#444" stroke-width="1.3"/></svg><div class="stat__num">Top 1%</div><div class="stat__lbl">Eligible Staynest homes</div></div>
    <div class="stat"><svg width="16" height="16" viewBox="0 0 24 24"><path d="M3 11l9-8 9 8v10H3z" fill="none" stroke="#444" stroke-width="1.3"/></svg><div class="stat__num">Prime Keeper</div><div class="stat__lbl">Hosted with Care</div></div>
  </div></div>

  <div class="a" style="left:61px;top:509px;width:30px;height:30px;border-left:2px solid var(--gold);border-top:2px solid var(--gold)"></div>
  <div class="a" style="left:303px;top:711px;width:30px;height:38px;border-right:2px solid var(--gold);border-bottom:2px solid var(--gold)"></div>
  <div class="ph ph--house" style="left:68px;top:515px;width:127px;height:232px" role="img" aria-label="House exterior with lawn"></div>
  <div class="ph ph--kitchen" style="left:201px;top:515px;width:127px;height:113px" role="img" aria-label="Kitchen and dining table"></div>
  <div class="ph ph--room" style="left:201px;top:633px;width:127px;height:114px" role="img" aria-label="Bedroom with window"></div>
  <div class="a eyebrow" style="left:360px;top:521px">Birch Lantern Retreat</div>
  <h2 class="a h2" style="left:360px;top:534px;width:230px;font-size:21px">Your Home Base for the Best of Bend</h2>
  <div class="a" style="left:360px;top:587px;font-size:8px;color:var(--green-dark);font-weight:500">Minutes from Bend's Tannery Row Quarter</div>
  <p class="a intro__para" style="left:360px;top:604px">Just steps from Bend's Tannery Row Quarter, Birch Lantern Retreat is a warm and inviting 3-bedroom retreat designed for relaxing, reconnecting, and making the most of your time in Central Oregon. Enjoy comfortable living spaces, a well-equipped kitchen, a cozy fireplace, and a private fenced backyard—all within an easy walk of restaurants, shopping, the Deschutes River, and Larkspur Fields Pavilion.</p>
  <div class="a check" style="left:358px;top:684px">Bedrooms</div>
  <div class="a check" style="left:358px;top:700px">Bathrooms</div>
  <div class="a check" style="left:435px;top:684px">Kitchen</div>
  <div class="a check" style="left:435px;top:700px">Living areas</div>
  <div class="a check" style="left:512px;top:679px">Backyard</div>
  <div class="a check" style="left:512px;top:695px">Pet Friendly</div>
  <div class="btn btn--dark" style="left:360px;top:726px;width:121px;height:26px;font-size:6.5px">Explore the House →</div>

  <div class="a features"></div>
  <div class="a" style="left:315px;top:786px;width:1px;height:44px;background:var(--gold)"></div>
  <h2 class="a h2 center" style="top:840px;text-align:center">Key Features</h2>
  <div class="fcard" style="left:65px;top:888px"><div class="fcard__icon"><svg width="18" height="18" viewBox="0 0 24 24"><path d="M4 18v-7h16v7M6 11V7h12v4M4 15h16" fill="none" stroke="#fff" stroke-width="1.5"/></svg></div>3 bedrooms</div>
  <div class="fcard" style="left:194px;top:888px"><div class="fcard__icon"><svg width="18" height="18" viewBox="0 0 24 24"><path d="M3 12h18v3a4 4 0 0 1-4 4H7a4 4 0 0 1-4-4zM6 12V5h3" fill="none" stroke="#fff" stroke-width="1.5"/></svg></div>2 bathrooms</div>
  <div class="fcard" style="left:323px;top:888px"><div class="fcard__icon"><svg width="18" height="18" viewBox="0 0 24 24"><rect x="4" y="5" width="16" height="14" fill="none" stroke="#fff" stroke-width="1.5"/><path d="M4 11h16" stroke="#fff" stroke-width="1.5"/></svg></div>Well-equipped<br>kitchen</div>
  <div class="fcard" style="left:452px;top:888px"><div class="fcard__icon"><svg width="18" height="18" viewBox="0 0 24 24"><path d="M12 20l-7-7a4 4 0 0 1 7-5 4 4 0 0 1 7 5z" fill="none" stroke="#fff" stroke-width="1.5"/></svg></div>Pet friendly</div>
  <div class="fcard" style="left:65px;top:998px"><div class="fcard__icon"><svg width="18" height="18" viewBox="0 0 24 24"><circle cx="12" cy="12" r="8" fill="none" stroke="#fff" stroke-width="1.5"/><path d="M12 7v5l3 2" fill="none" stroke="#fff" stroke-width="1.5"/></svg></div>Approximately a<br>5-minute walk to Bend's<br>Tannery Row Quarter</div>
  <div class="fcard" style="left:194px;top:998px"><div class="fcard__icon"><svg width="18" height="18" viewBox="0 0 24 24"><path d="M5 19V8l2-2 2 2v11M11 19V8l2-2 2 2v11M17 19V8l2-2 2 2v11M3 12h19M3 16h19" fill="none" stroke="#fff" stroke-width="1.3"/></svg></div>Private fenced<br>backyard</div>
  <div class="fcard" style="left:323px;top:998px"><div class="fcard__icon"><svg width="18" height="18" viewBox="0 0 24 24"><path d="M3 19l6-10 4 6 3-4 5 8z" fill="none" stroke="#fff" stroke-width="1.5"/></svg></div>Covered<br>outdoor area</div>
  <div class="fcard" style="left:452px;top:998px"><div class="fcard__icon"><svg width="18" height="18" viewBox="0 0 24 24"><path d="M3 11l9-6 9 6v9H3zM7 20v-6h10v6" fill="none" stroke="#fff" stroke-width="1.5"/></svg></div>Off-street driveway<br>parking</div>

  <div class="a eyebrow" style="left:67px;top:1210px">Inside Birch Lantern Retreat</div>
  <h2 class="a h2" style="left:67px;top:1226px;width:220px">Relax, Recharge &amp;<br>Feel at Home</h2>
  <p class="a" style="left:308px;top:1222px;width:270px;font-size:8.6px;line-height:13px;color:var(--muted)">Thoughtfully designed for comfort and easy vacation living, Birch Lantern Retreat offers welcoming spaces to gather, unwind and enjoy your stay in Bend.</p>
  <div class="tile" style="left:69px;top:1296px;width:167px;height:147px"><div class="ph ph--room" role="img" aria-label="Bedroom 1 with queen bed"></div><span class="tile__lbl">Bedroom 1</span></div>
  <div class="tile" style="left:239px;top:1296px;width:167px;height:147px"><div class="ph ph--teal" role="img" aria-label="Bedroom 2 with teal dresser"></div><span class="tile__lbl">Bedroom 2</span></div>
  <div class="tile" style="left:409px;top:1296px;width:167px;height:147px"><div class="ph ph--room" role="img" aria-label="Bedroom 3 with wooden dresser"></div><span class="tile__lbl">Bedroom 3</span></div>
  <div class="tile" style="left:69px;top:1447px;width:167px;height:191px"><div class="ph ph--kitchen" role="img" aria-label="Kitchen with white cabinets"></div><span class="tile__lbl">Kitchen</span></div>
  <div class="tile" style="left:239px;top:1447px;width:337px;height:191px"><div class="ph ph--room" role="img" aria-label="Bright main room with bed and dresser"></div><span class="tile__lbl">Living Room</span></div>
  <div class="tile" style="left:69px;top:1644px;width:167px;height:146px"><div class="ph ph--kitchen" role="img" aria-label="Dining table with chairs"></div><span class="tile__lbl">Dinning Room</span></div>
  <div class="tile" style="left:239px;top:1644px;width:167px;height:146px"><div class="ph" role="img" aria-label="Bathroom with shower"></div><span class="tile__lbl">Bathroom</span></div>
  <div class="tile" style="left:409px;top:1644px;width:167px;height:146px"><div class="ph ph--kitchen" role="img" aria-label="Living room with fireplace and sofa"></div><span class="tile__lbl">Living room</span></div>

  <div class="a outdoor"></div>
  <div class="a eyebrow" style="left:72px;top:1894px">Outdoor Living</div>
  <h2 class="a h2" style="left:67px;top:1910px;color:#fff">A Backyard Made<br>for Everyone</h2>
  <p class="a" style="left:67px;top:1968px;width:228px;font-size:6.6px;line-height:10px;color:#e8ecdf">Unwind in your own private outdoor space. The fully fenced backyard offers a comfortable place to relax, gather around the fire, or let your four-legged companion enjoy the outdoors.</p>
  <div class="ofeat" style="left:67px;top:2020px"><i></i>Sleeps up to 6 guests</div>
  <div class="ofeat" style="left:192px;top:2020px"><i></i>Fireplace</div>
  <div class="ofeat" style="left:67px;top:2047px"><i></i>Covered Outdoor Area</div>
  <div class="ofeat" style="left:192px;top:2047px"><i></i>Pet Friendly</div>
  <div class="ofeat" style="left:67px;top:2076px"><i></i>Fully Fenced Yard</div>
  <div class="ofeat" style="left:192px;top:2076px"><i></i>Outdoor Gathering Space</div>
  <div class="a" style="left:349px;top:1866px;width:235px;height:235px;border-radius:50%;border:5px solid var(--gold);background:linear-gradient(160deg,#8aa0b4,#6d7a4a 50%,#4b6a2a)" role="img" aria-label="Backyard with patio umbrella, rocks and water feature"></div>
  <div class="a" style="left:327px;top:2008px;width:122px;height:122px;border-radius:50%;border:4px solid #f2efe6;background:linear-gradient(160deg,#9a8c76,#c98a3e 55%,#6d6253)" role="img" aria-label="Fire table with patio chairs"></div>
</div>

<div class="column column--right">
  <div class="a location"></div>
  <div class="a eyebrow center" style="top:31px;text-align:center">Location</div>
  <h2 class="a h2 center" style="top:44px;text-align:center">Walk to the Best of Bend</h2>
  <p class="a" style="left:125px;top:80px;width:380px;text-align:center;font-size:7.5px;line-height:13px;color:var(--muted)">Stay close to everything that makes Bend special. Birch Lantern Retreat puts dining, entertainment, shopping and outdoor adventures within easy reach.</p>
  <div class="lcard" style="left:61px"><div class="lcard__frame"></div><svg width="22" height="30" viewBox="0 0 22 30"><circle cx="12" cy="4" r="3" fill="none" stroke="#444"/><path d="M12 8l-3 8 4 4-2 8M10 16l-5 10M12 10l5 4" fill="none" stroke="#444"/></svg><b>5-Minute Walk</b><br>Tannery Row Quarter</div>
  <div class="lcard" style="left:194px"><div class="lcard__frame"></div><svg width="36" height="30" viewBox="0 0 36 30"><path d="M3 12Q18 0 33 12v16H3zM8 28V16h20v12" fill="none" stroke="#444"/></svg><b>Nearby</b><br>Larkspur Fields<br>Pavilion</div>
  <div class="lcard" style="left:322px"><div class="lcard__frame"></div><svg width="36" height="30" viewBox="0 0 36 30"><path d="M2 28l10-18 6 10 5-7 11 15zM6 14l3-8 3 8" fill="none" stroke="#444"/></svg><b>Minutes Away</b><br>Deschutes River<br>&amp; Trails</div>
  <div class="lcard" style="left:455px"><div class="lcard__frame"></div><svg width="34" height="30" viewBox="0 0 34 30"><path d="M3 10h28l-3-7H6zM5 10v18h24V10M12 28v-9h10v9" fill="none" stroke="#444"/></svg><b>Close to</b><br>Restaurants,<br>Breweries &amp; Shopping</div>

  <div class="a eyebrow center" style="top:319px;text-align:center">Photos</div>
  <h2 class="a h2 center" style="top:332px;text-align:center">Our Gallery</h2>
  <div class="ph ph--yard" style="left:5px;top:376px;width:207px;height:136px" role="img" aria-label="Backyard with rocks and fence"></div>
  <div class="ph ph--house" style="left:216px;top:376px;width:203px;height:136px" role="img" aria-label="House front view"></div>
  <div class="ph ph--patio" style="left:422px;top:376px;width:204px;height:304px" role="img" aria-label="Patio chairs under tall pine"></div>
  <div class="ph ph--teal" style="left:5px;top:516px;width:414px;height:164px" role="img" aria-label="Bedroom with teal dresser and TV"></div>
  <div class="ph ph--room" style="left:5px;top:684px;width:207px;height:136px" role="img" aria-label="Hallway with shelves"></div>
  <div class="ph" style="left:216px;top:684px;width:203px;height:136px" role="img" aria-label="Bathroom vanity"></div>
  <div class="ph ph--room" style="left:422px;top:684px;width:204px;height:136px" role="img" aria-label="Bedroom with chandelier"></div>

  <div class="a testimonials"></div>
  <div class="a eyebrow center" style="top:858px;text-align:center">Testimonials</div>
  <h2 class="a h2 center" style="top:871px;text-align:center">Read Guests. Real Reviews</h2>
  <div class="a center" style="top:908px;text-align:center;font-size:7.5px;font-weight:600"><span style="color:var(--gold);letter-spacing:1px">★★★★★</span> 4.98-star rating and 200+ guest reviews</div>
  <div class="arrow" style="left:26px;top:994px">‹</div>
  <div class="arrow" style="left:578px;top:994px">›</div>
  <div class="review" style="left:58px"><div class="review__av"></div><div class="review__name">Dana</div><div style="font-size:5px">6 years on Staynest</div><div class="review__stars">★★★★★</div>This place is amazing and the personal touches were over the top! Rosa was so kind and communicative. Great location, great house and we will definitely be back!</div>
  <div class="review" style="left:230px"><div class="review__av"></div><div class="review__name">Maribel</div><div style="font-size:5px">Salem, Oregon</div><div class="review__stars">★★★★★</div>Great house in Bend, charming and very clean. Quiet neighborhood—we enjoyed our stay here. Ample parking. Well equipped kitchen. Bathrooms had extra amenities that ...</div>
  <div class="review" style="left:403px"><div class="review__av"></div><div class="review__name">Talia</div><div style="font-size:5px">Saint Paul, Minnesota</div><div class="review__stars">★★★★★</div>Great location with lots of thoughtful touches! We would definitely stay here again!</div>

  <h2 class="a h2 center" style="top:1150px;text-align:center">Frequently Asked Questions</h2>
  <div class="faq__row" style="top:1204px">Is Birch Lantern Retreat pet friendly?</div>
  <div class="faq__row" style="top:1238px">How many guests can the home accommodate?</div>
  <div class="faq__row" style="top:1272px">How close is Birch Lantern Retreat to the Tannery Row Quarter?</div>
  <div class="faq__row" style="top:1306px">Is parking available at the property?</div>
  <div class="faq__row" style="top:1340px">How do I check availability and book?</div>
  <div class="faq__row" style="top:1374px;border-bottom:0">What attractions are nearby?</div>

  <div class="a cta">
    <div class="a eyebrow center" style="top:37px;text-align:center">Ready for your Bend getaway?</div>
    <h2 class="a h2 center" style="top:50px;text-align:center;color:#fff;font-size:25px">Check Availability &amp; Book Direct</h2>
    <p class="a center" style="top:86px;text-align:center;font-size:7px;color:#e6eadc">Plan your stay at Birch Lantern Retreat and enjoy a simple, secure direct-booking experience.</p>
    <div class="a form">
      <div class="form__field"><small>CHECK IN</small>Select Date</div>
      <div class="form__field"><small>CHECK OUT</small>Select Date</div>
      <div class="form__field" style="border-right:0"><small>GUESTS</small>2 Guests</div>
      <div class="btn btn--gold" style="position:relative;width:110px;height:30px;font-size:6px">Check Availability →</div>
    </div>
  </div>

  <div class="a brand" style="left:62px;top:1713px;color:var(--ink);font-size:9px">BIRCH LANTERN RETREAT</div>
  <div class="social" style="left:112px"></div><div class="social" style="left:128px"></div><div class="social" style="left:144px"></div>
  <div class="a" style="left:216px;top:1688px;width:1px;height:96px;background:var(--line)"></div>
  <div class="a foot__head" style="left:248px;top:1688px">EXPLORE</div>
  <div class="a foot__list" style="left:248px;top:1706px">The House<br>Photo Gallery<br>Explore Bend<br>Guest Reviews<br>Availability<br>FAQ<br>Contact</div>
  <div class="a foot__head" style="left:335px;top:1688px">YOUR STAY</div>
  <div class="a foot__list" style="left:335px;top:1706px">Pet Friendly<br>Private Fenced Backyard<br>Off-Street Parking<br>Check-In / Check-Out<br>Cancellation Policy<br>House Rules</div>
  <div class="a foot__head" style="left:445px;top:1688px">CONTACT US</div>
  <div class="a foot__list" style="left:445px;top:1710px;line-height:21.5px;padding-left:24px">Bend, Oregon, United States<br>+1 541 555 0142<br>booking@birchlantern.example</div>
  <div class="a" style="left:446px;top:1711px;width:16px;height:16px;border:1px solid var(--line)"></div>
  <div class="a" style="left:446px;top:1732px;width:16px;height:16px;border:1px solid var(--line)"></div>
  <div class="a" style="left:446px;top:1754px;width:16px;height:16px;border:1px solid var(--line)"></div>
  <div class="a" style="left:70px;top:1817px;width:492px;height:1px;background:var(--line)"></div>
  <div class="a" style="left:70px;top:1827px;font-size:5px;color:var(--muted)">© 2026 Birch Lantern Retreat. All Rights Reserved.</div>
  <div class="a" style="right:69px;top:1827px;font-size:5px;color:var(--muted)">Privacy Policy | Terms &amp; Conditions | Cancellation Policy</div>
</div>

</div>
</body>
</html>
```